Meridale Bed Company Needs Business Card

Looking for a very nice looking business card. Creative but not extravagant. We sell beds and pillows across the U.S. and need something professional but catchy. I have attached the logo.

Name : Devin Holt
Title : President
Phone : (800) 471-2960
Email: sleep@quilmora.com
Website: www.quilmora.com

Can be single-sided or double-sided
horizontal or vertical

Can use Blues/Greys

Target Market(s)

Mass Market

Industry/Entity Type

Retail

Contact Information for Business Card

Name : Devin Holt
Title : President
Phone : (800) 471-2960
Email: sleep@quilmora.com
Website: www.quilmora.com

Requirements
Must have
• Clean, Modern, Smooth
• Can use Blues/Greys
• On the other side without the information - have something simple like www.quilmora.com or our logo
Nice to have
• Surprise me
Should not have
• Nothing crazy, nothing cluttered

```html
<!DOCTYPE html>
<html lang="en">
<head>
<meta charset="utf-8">
<title>Quilmora Business Card</title>
<link rel="stylesheet" href="https://fonts.googleapis.com/css2?family=Nunito+Sans:wght@400;700&display=swap">
<style>
  :root {
    --backdrop: #d4d4d4;
    --brand-blue: #35a4d4;
    --paper-white: #ffffff;
    --pale-blue: #e8f0fc;
  }
  html, body {
    margin: 0;
    padding: 0;
    width: 1200px;
    height: 1200px;
    overflow: hidden;
    background: var(--backdrop);
  }
  .canvas {
    position: relative;
    width: 1200px;
    height: 1200px;
  }
  .card {
    position: absolute;
    top: 208px;
    width: 347px;
    height: 607px;
    transform: scale(1.2);
    transform-origin: 0 0;
    background: var(--brand-blue);
    overflow: hidden;
    font-family: "Nunito Sans", "Avenir Next", sans-serif;
    color: var(--paper-white);
  }
  .card--front { left: 122px; }
  .card--back { left: 666px; }
  .card__art {
    position: absolute;
    inset: 0;
    width: 100%;
    height: 100%;
  }
  .brand-name {
    position: absolute;
    left: 0;
    right: 0;
    top: 444px;
    margin: 0;
    text-align: center;
    font-family: "Nunito Sans", sans-serif;
    font-weight: 400;
    font-size: 48px;
    line-height: 1;
    color: var(--paper-white);
  }
  .identity {
    position: absolute;
    left: 23px;
    top: 27px;
    height: 54px;
    padding-left: 23px;
    border-left: 10px solid var(--paper-white);
  }
  .identity__name {
    margin: -1px 0 0;
    font-size: 27px;
    font-weight: 400;
    line-height: 30px;
  }
  .identity__name strong { font-weight: 700; }
  .identity__title {
    margin: 4px 0 0 3px;
    font-size: 15px;
    letter-spacing: 0.5px;
    line-height: 18px;
  }
  .contact {
    position: absolute;
    left: 22px;
    top: 0;
    margin: 0;
    padding: 0;
    list-style: none;
  }
  .contact__item {
    position: absolute;
    display: flex;
    align-items: center;
    white-space: nowrap;
    font-size: 16px;
  }
  .contact__item--email { top: 137px; }
  .contact__item--phone { top: 216px; }
  .contact__item--web { top: 296px; }
  .contact__icon {
    width: 38px;
    height: 30px;
    margin-right: 16px;
    flex: none;
  }
</style>
</head>
<body>
<main class="canvas">
  <section class="card card--front" aria-label="Card front">
    <svg class="card__art" viewBox="0 0 347 607" aria-hidden="true">
      <polygon points="168,0 262,0 198,349" fill="var(--pale-blue)"/>
      <polygon points="269,0 347,0 347,114 203,350" fill="var(--paper-white)"/>
    </svg>
    <p class="brand-name">quilmora</p>
  </section>

  <section class="card card--back" aria-label="Card back">
    <svg class="card__art" viewBox="0 0 347 607" aria-hidden="true">
      <polygon points="0,572 347,235 347,607 0,607" fill="var(--paper-white)"/>
      <polygon points="0,576 347,352 347,364 0,583" fill="var(--brand-blue)"/>
    </svg>

    <div class="identity">
      <h1 class="identity__name">Devin <strong>Holt</strong></h1>
      <p class="identity__title">PRESIDENT</p>
    </div>

    <ul class="contact">
      <li class="contact__item contact__item--email">
        <svg class="contact__icon" viewBox="0 0 38 30" aria-hidden="true">
          <rect x="2" y="5" width="34" height="20" fill="none" stroke="#fff" stroke-width="2"/>
          <path d="M7 10 L19 17 L31 10" fill="none" stroke="#fff" stroke-width="2"/>
        </svg>
        sleep@quilmora.com
      </li>
      <li class="contact__item contact__item--phone">
        <svg class="contact__icon" viewBox="0 0 38 30" aria-hidden="true">
          <path d="M9 22 C6 18 10 12 16 7 C21 3 27 1 30 4 L27 8 L23 6 C18 9 14 13 12 18 L14 22 Z" fill="none" stroke="#fff" stroke-width="2" stroke-linejoin="round"/>
          <path d="M9 22 L7 28" stroke="#fff" stroke-width="2" stroke-linecap="round"/>
        </svg>
        (800) 471-2960
      </li>
      <li class="contact__item contact__item--web">
        <svg class="contact__icon" viewBox="0 0 38 30" aria-hidden="true">
          <circle cx="17" cy="15" r="13" fill="none" stroke="#fff" stroke-width="2"/>
          <ellipse cx="17" cy="15" rx="6" ry="13" fill="none" stroke="#fff" stroke-width="2"/>
          <path d="M4 15 H30 M6 9 H28 M6 21 H28 M17 2 V28" stroke="#fff" stroke-width="2"/>
        </svg>
        www.quilmora.com
      </li>
    </ul>
  </section>
</main>
</body>
</html>
```